Stylish new business card needed!

Hello everyone! I am in need of a new business card design for an alarm company here in Hurricane WV. I have all fonts, color codes and logos provided for you use! We are a young company and like the style of a clean sleek looking business card. Would like it double sided, one side holding the logo and the other with your design!
Target Market(s)
The people that are looking for the newest tech for home automation and security
Industry/Entity Type
Alarm services; Home automation
Contact Information for Business Card
Name of person; position (Sales; Installer); Phone Number (555.418.7260); Employee cell Number; Website (www.GuardedByVelk.example); Employee Email; Double sided
Look and feel
Each slider illustrates characteristics of the customer's brand and the style your logo design should communicate.

```html
<!DOCTYPE html>
<html lang="en">
<head>
<meta charset="utf-8">
<title>Velk Business Card</title>
<link href="https://fonts.googleapis.com/css2?family=Arimo:wght@400;700&display=swap" rel="stylesheet">
<style>
  :root {
    --orange: #f5904f;
    --grey: #9b9b9b;
    --ink: #1a1a1a;
    --white: #ffffff;
    --stage: #2a2a2a;
  }
  * { box-sizing: border-box; margin: 0; padding: 0; }
  html, body {
    width: 1200px; height: 880px; overflow: hidden;
    background: var(--stage);
    font-family: "Arimo", Arial, sans-serif;
  }
  .canvas {
    width: 1200px; height: 880px;
    display: flex; flex-direction: column; align-items: center; justify-content: center;
    gap: 48px;
  }
  .card {
    position: relative;
    width: 560px; height: 320px;
    overflow: hidden;
    box-shadow: 0 10px 28px rgba(0,0,0,.55);
  }
  /* Logo side */
  .card--brand {
    background: var(--orange);
    color: var(--white);
    display: flex; flex-direction: column; align-items: center; justify-content: center;
  }
  .brand-name {
    font-weight: 700;
    font-size: 96px;
    letter-spacing: 6px;
    line-height: 1;
  }
  .brand-tagline {
    margin-top: 14px;
    font-weight: 700;
    font-size: 12px;
    letter-spacing: 2px;
    text-transform: uppercase;
  }
  /* Contact side */
  .card--contact { background: var(--white); }
  .wave { position: absolute; left: 0; top: 0; width: 560px; height: 320px; }
  .contact-logo {
    position: absolute; top: 34px; right: 40px;
    font-weight: 700; font-size: 56px; letter-spacing: 4px;
    color: var(--grey); line-height: 1;
  }
  .person {
    position: absolute; left: 40px; top: 86px;
  }
  .person-name {
    font-weight: 700; font-size: 22px; letter-spacing: 1.5px;
    color: var(--grey); text-transform: uppercase;
  }
  .person-name .surname { color: var(--orange); }
  .person-role {
    margin-top: 4px; font-size: 15px; color: var(--ink);
  }
  .contact-list {
    position: absolute; left: 58px; top: 156px;
    list-style: none;
  }
  .contact-list li {
    display: flex; align-items: center; gap: 8px;
    height: 21px; font-size: 14px; color: var(--ink);
  }
  .contact-list svg { width: 13px; height: 13px; flex: none; }
</style>
</head>
<body>
<main class="canvas">
  <section class="card card--brand" aria-label="Card logo side">
    <div class="brand-name">VELK</div>
    <div class="brand-tagline">Automation and Security Services</div>
  </section>

  <section class="card card--contact" aria-label="Card contact side">
    <svg class="wave" viewBox="0 0 560 320" aria-hidden="true">
      <path d="M0,290 C220,292 360,262 440,200 C500,152 530,132 560,124" fill="none" stroke="var(--grey)" stroke-width="6"/>
      <path d="M0,300 C220,302 365,274 445,212 C505,164 532,144 560,138 L560,320 L0,320 Z" fill="var(--orange)"/>
    </svg>

    <div class="contact-logo">VELK</div>

    <div class="person">
      <div class="person-name">Dale <span class="surname">Marrow</span></div>
      <div class="person-role">Sales; Installer</div>
    </div>

    <ul class="contact-list">
      <li>
        <svg viewBox="0 0 16 16" aria-hidden="true"><path d="M2 6c0-2 3-3 6-3s6 1 6 3l-3 1-1-2H6L5 7z M4 8h8l1 5H3z" fill="var(--orange)"/></svg>
        555.418.7260
      </li>
      <li>
        <svg viewBox="0 0 16 16" aria-hidden="true"><rect x="4" y="1" width="8" height="14" rx="1.5" fill="none" stroke="var(--orange)" stroke-width="1.8"/></svg>
        555.418.7269
      </li>
      <li>
        <svg viewBox="0 0 16 16" aria-hidden="true"><rect x="1" y="3" width="14" height="10" fill="var(--orange)"/><path d="M1 3l7 6 7-6" fill="none" stroke="var(--white)" stroke-width="1.2"/></svg>
        info@GuardedByVelk.example
      </li>
      <li>
        <svg viewBox="0 0 16 16" aria-hidden="true"><circle cx="8" cy="8" r="7" fill="var(--orange)"/><path d="M1 8h14M8 1c3 3 3 11 0 14M8 1c-3 3-3 11 0 14" fill="none" stroke="var(--white)" stroke-width="1"/></svg>
        www.GuardedByVelk.example
      </li>
    </ul>
  </section>
</main>
</body>
</html>
```